Staff Newsletter Template Image

We are looking for two .jpg images that we can put into a Word document and use for our staff newsletter. We will then add content using text boxes.
Attached is the current template which works for the columns and size that we need but we just want a fresh new design.
The Word document shows how we use it.
The name will stay the same - Brightwave Post but can be a different look to the current one.

Target Market(s)

Sales team

Colors

Designer to choose colors to be used in the design.

Requirements
Must have
• Colours will be green, grey and white, possibly cream if needed. All from the guidelines.
• I have attached our brand guidelines which shows design elements and fonts for our brand. Also attached is brand guidelines for one of our product lines as we would like to use the same green.
• It needs to be nice to look at and motivational for our team

```html
<!DOCTYPE html>
<html lang="en">
<head>
<meta charset="utf-8">
<title>Brightwave Post – Staff Newsletter</title>
<link rel="stylesheet" href="https://fonts.googleapis.com/css2?family=Open+Sans:wght@600&display=swap">
<style>
  :root {
    --brand-green: #8cc540;
    --brand-charcoal: #3b3c3e;
    --paper-white: #ffffff;
  }
  * { margin: 0; padding: 0; box-sizing: border-box; }
  html, body {
    width: 884px;
    height: 1200px;
    overflow: hidden;
    background: var(--paper-white);
  }
  .newsletter-page {
    position: relative;
    width: 884px;
    height: 1200px;
    overflow: hidden;
    background: var(--paper-white);
  }
  .page-artwork {
    position: absolute;
    inset: 0;
    width: 884px;
    height: 1200px;
    display: block;
  }
  .band-green { fill: var(--brand-green); }
  .band-charcoal { fill: var(--brand-charcoal); }
  .content-area { fill: var(--paper-white); }
  .masthead {
    position: absolute;
    left: 30px;
    top: 74px;
    display: flex;
    align-items: center;
    gap: 10px;
  }
  .masthead-dot {
    width: 14px;
    height: 14px;
    border-radius: 50%;
    background: var(--paper-white);
    flex: none;
  }
  .masthead-name {
    font-family: "Open Sans", Arial, sans-serif;
    font-weight: 600;
    font-size: 24px;
    line-height: 1;
    letter-spacing: 0;
    color: var(--paper-white);
    white-space: nowrap;
  }
</style>
</head>
<body>
  <main class="newsletter-page">
    <svg class="page-artwork" viewBox="0 0 578 785" preserveAspectRatio="none" aria-hidden="true">
      <rect class="band-green" x="0" y="0" width="578" height="260"/>
      <path class="band-charcoal" d="M0,118 Q250,58 578,72 Q400,80 230,112 Q100,138 0,178 Z"/>
      <path class="content-area" d="M0,222 Q210,108 578,78 L578,785 L0,785 Z"/>
      <path class="band-green" d="M0,748 Q340,742 578,678 L578,785 L0,785 Z"/>
    </svg>
    <header class="masthead">
      <span class="masthead-dot" aria-hidden="true"></span>
      <h1 class="masthead-name">Brightwave Post</h1>
    </header>
  </main>
</body>
</html>
```